Travel Agency Website - Simple General

Need a 7 page simple design that is pretty repetitive. Need to be able to load quickly that is SEO optimized. Trying to give ideas on what they can do, be personal as we are local, but at the same time come across as professional and get information easily with little burden.

- Landing Page
- Brimwell Vacations Page
- Family Trips
- Road Trips from Texas
- Other Destinations
- About Us Page
- Contact Us Page

Target Market(s)

Families

Coding

Coded - Design and coding required

Number of Pages Required

5+ page

Colors

Designer to choose colors to be used in the design.

Requirements
Must have
• Like it to flow easily with our logo. Use that for colors, etc.

```html
<!DOCTYPE html>
<html lang="en">
<head>
<meta charset="utf-8">
<title>Meadowlark Wander Travel Co.</title>
<link href="https://fonts.googleapis.com/css2?family=Figtree:wght@400;500;600&display=swap" rel="stylesheet">
<style>
:root{
  --teal:#1f7a78;
  --teal-dark:#1a5f68;
  --gold:#c29a55;
  --cream:#fdf8f3;
  --ink:#2b2b2b;
  --rule:#e2ddd6;
}
*{margin:0;padding:0;box-sizing:border-box}
html,body{width:1200px;height:838px;overflow:hidden;background:var(--cream);font-family:"Figtree",sans-serif}
.page{position:relative;width:1200px;height:838px}
.topbar{position:absolute;top:0;left:0;width:1200px;height:43px;display:flex}
.topbar .left{width:604px;background:var(--teal);display:flex;align-items:center;padding-left:90px;gap:9px;color:#fff;font-size:13.5px;font-weight:500}
.topbar .right{flex:1;background:var(--gold);display:flex;align-items:center;justify-content:flex-end;padding-right:89px;gap:9px;color:#fff;font-size:16px;font-weight:500}
.icon-dot{width:25px;height:25px;border-radius:50%;background:#fff;display:flex;align-items:center;justify-content:center}
.nav{position:absolute;top:82px;font-size:15px;font-weight:500;color:var(--teal-dark);display:flex}
.nav a{color:inherit;text-decoration:none;position:relative}
.nav.left{left:79px;gap:22px}
.nav.right{left:757px;gap:28px}
.nav .active::before{content:"";position:absolute;left:50%;top:-20px;width:14px;height:16px;transform:translateX(-50%);
  background:var(--gold);clip-path:polygon(50% 0,60% 40%,100% 50%,60% 60%,50% 100%,40% 60%,0 50%,40% 40%)}
.brand{position:absolute;left:520px;top:20px;width:174px;height:150px;border-radius:40px;background:#eef4ef;border:3px solid #fff;
  box-shadow:0 0 0 2px #cfe0da;z-index:2;display:flex;flex-direction:column;align-items:center;justify-content:center;text-align:center;
  color:var(--teal-dark);font-weight:600;font-size:22px;line-height:1.1}
.brand small{font-size:8px;letter-spacing:1.5px;margin-top:8px;font-weight:600}
.grid{position:absolute;left:72px;top:135px;width:1068px;height:597px;display:grid;grid-template-columns:1fr 1fr;grid-template-rows:1fr 1fr;gap:3px}
.card{position:relative;overflow:hidden}
.card .photo{position:absolute;inset:0}
.card h2{position:absolute;left:34px;bottom:26px;color:#fff;font-size:31px;font-weight:500;text-shadow:0 1px 4px rgba(0,0,0,.35)}
.card .go{position:absolute;right:11px;bottom:13px;width:34px;height:34px;border-radius:50%;background:var(--teal);display:flex;align-items:center;justify-content:center}
.p1{background:linear-gradient(180deg,#3f93e0 0%,#4a7fc4 55%,#2e3a55 100%)}
.p2{background:linear-gradient(180deg,#8a8c7a 0%,#7a8f86 40%,#6f95a6 65%,#4e5a55 100%)}
.p3{background:linear-gradient(180deg,#8fc0e8 0%,#b9d3e6 50%,#8b9bab 100%)}
.p4{background:linear-gradient(120deg,#d98a5a 0%,#e4b35a 35%,#c9766a 60%,#2aa0d8 100%)}
.footer{position:absolute;left:0;top:773px;width:1200px;border-top:1px solid var(--rule);height:65px}
.footer p{position:absolute;left:0;right:0;top:19px;text-align:center;font-size:15px;color:var(--ink);letter-spacing:.3px}
.social{position:absolute;top:17px;left:1071px;display:flex;gap:7px}
.social span{width:24px;height:24px;border-radius:50%;background:var(--teal)}
</style>
</head>
<body>
<div class="page">
  <header class="topbar">
    <div class="left">
      <span class="icon-dot"><svg width="14" height="10" viewBox="0 0 14 10"><rect x="0.7" y="0.7" width="12.6" height="8.6" rx="1" fill="none" stroke="#1f7a78" stroke-width="1.4"/><path d="M1 1l6 5 6-5" fill="none" stroke="#1f7a78" stroke-width="1.4"/></svg></span>
      MeadowlarkWander@mailbox.com
    </div>
    <div class="right">
      <span class="icon-dot"><svg width="13" height="13" viewBox="0 0 24 24"><path fill="#c29a55" d="M6.6 10.8a15.1 15.1 0 006.6 6.6l2.2-2.2c.3-.3.7-.4 1-.2 1.1.4 2.3.6 3.6.6.6 0 1 .4 1 1V20c0 .6-.4 1-1 1C10.6 21 3 13.4 3 4c0-.6.4-1 1-1h3.5c.6 0 1 .4 1 1 0 1.3.2 2.5.6 3.6.1.3 0 .7-.2 1z"/></svg></span>
      Phone Number (555) 014 2290
    </div>
  </header>

  <nav class="nav left">
    <a class="active" href="#">Home</a>
    <a href="#">Brimwell Vacations</a>
    <a href="#">Family Trips</a>
    <a href="#">Texas Road Trips</a>
  </nav>
  <div class="brand">Meadowlark<br>Wander<small>TRAVEL CO.</small></div>
  <nav class="nav right">
    <a href="#">Other Destinations</a>
    <a href="#">About Us</a>
    <a href="#">Contact us</a>
  </nav>

  <main class="grid">
    <a class="card" href="#">
      <div class="photo p1" role="img" aria-label="Palm-lined theme park entrance arch under a blue sky"></div>
      <h2>Brimwell Vacations</h2>
      <span class="go"><svg width="16" height="16" viewBox="0 0 16 16"><path d="M3 13L13 3M5 3h8v8" fill="none" stroke="#fff" stroke-width="2"/></svg></span>
    </a>
    <a class="card" href="#">
      <div class="photo p2" role="img" aria-label="Camper van on a coastal road with mountains behind"></div>
      <h2>Texas Road Trips</h2>
      <span class="go"><svg width="16" height="16" viewBox="0 0 16 16"><path d="M3 13L13 3M5 3h8v8" fill="none" stroke="#fff" stroke-width="2"/></svg></span>
    </a>
    <a class="card" href="#">
      <div class="photo p3" role="img" aria-label="Happy family in sun hats against a bright sky"></div>
      <h2>Family Trips</h2>
      <span class="go"><svg width="16" height="16" viewBox="0 0 16 16"><path d="M3 13L13 3M5 3h8v8" fill="none" stroke="#fff" stroke-width="2"/></svg></span>
    </a>
    <a class="card" href="#">
      <div class="photo p4" role="img" aria-label="Colourful cliffside village above a blue sea"></div>
      <h2>Other Destinations</h2>
      <span class="go"><svg width="16" height="16" viewBox="0 0 16 16"><path d="M3 13L13 3M5 3h8v8" fill="none" stroke="#fff" stroke-width="2"/></svg></span>
    </a>
  </main>

  <footer class="footer">
    <p>© 2026 Meadowlark Wander. All Right Reserved</p>
    <div class="social"><span aria-label="Social profile"></span><span aria-label="Social profile"></span></div>
  </footer>
</div>
</body>
</html>
```